Real Estate Company Looking for Business Card Designs for 3 Executives

Hello!
Thanks so much for considering our project! We are a real estate investment company located in Edmonton, Alberta called Bellhaven Group of Companies. We invest/develop both commercial and residential real estate and are looking to create 3 DOUBLE-SIDED business cards for 3 top executives in the company! (for some reason it won't let us select the double-sided option, but yes, the cards are double sided and would be happy to tip extra)

We have certain guidelines that we want our business cards to for sure follow - the back of the Business card has to be the Black Background Version of the Logo which has already been designed and linked as a file (first file). We want the entire back of the card to simply just be the black background logo. In terms of the front of the card, would like to see a smaller version of the white background logo (linked as the second file) in the top left hand corner - of course, feel free to get creative and we can make revisions together along the way! and Then after that, just text. We want the card to be sharp, clean, easy on the eyes and highly professional looking. We would like the card to include the Full name of the Company (Bellhaven Group of Companies), Name of the Person, Title, Phone, Email. If possible please provide the front part of the card for 3 people:

1) Bellhaven Group of Companies, Liora Quenby, Chief Financial Officer, 780-555-0142, lioraquenby@bellhavengroup.example

2) Bellhaven Group of Companies, Tobias Quenby, Chief Executive Officer, 780-555-0187, tobiasquenby@bellhavengroup.example

3) Bellhaven Group of Companies, Rui Delcourt, Chief Operations Officer, 587-555-0163, ruidelcourt@bellhavengroup.example

Thank you so much for considering our project & we look forward to seeing your designs!

```html
<!DOCTYPE html>
<html lang="en">
<head>
<meta charset="utf-8">
<title>Bellhaven Business Card</title>
<link rel="stylesheet" href="https://fonts.googleapis.com/css2?family=Montserrat:wght@500;700&family=Arimo:wght@400&family=Jost:wght@400&display=swap">
<style>
  :root {
    --stage: #c9c9c9;
    --ink: #0b0708;
    --paper: #ffffff;
    --mist: #f1f5f5;
    --shadow: rgba(0, 0, 0, 0.28);
  }
  * { margin: 0; padding: 0; box-sizing: border-box; }
  html, body {
    width: 1200px;
    height: 800px;
    overflow: hidden;
    background: var(--stage);
  }
  .canvas {
    position: relative;
    width: 1200px;
    height: 800px;
    display: flex;
    align-items: center;
    justify-content: center;
    gap: 40px;
  }
  .card {
    position: relative;
    width: 540px;
    height: 310px;
    border-radius: 22px;
    overflow: hidden;
    box-shadow: 0 12px 30px var(--shadow);
  }
  /* Front */
  .card-front { background: var(--paper); color: var(--ink); }
  .front-corner-block {
    position: absolute;
    top: 0;
    right: 0;
    width: 112px;
    height: 56px;
    background: var(--ink);
  }
  .person {
    position: absolute;
    left: 30px;
    top: 58px;
  }
  .person-name {
    font-family: "Montserrat", sans-serif;
    font-weight: 700;
    font-size: 25px;
    letter-spacing: 0.5px;
    text-transform: uppercase;
    line-height: 1.1;
  }
  .person-title {
    font-family: "Arimo", sans-serif;
    font-size: 16px;
    margin-top: 2px;
  }
  .contact-band {
    position: absolute;
    left: 0;
    top: 150px;
    width: 350px;
    height: 118px;
    background: var(--ink);
    color: var(--paper);
    padding: 18px 0 0 28px;
    list-style: none;
  }
  .contact-item {
    display: flex;
    align-items: center;
    gap: 8px;
    font-family: "Arimo", sans-serif;
    font-size: 16px;
    line-height: 27px;
    white-space: nowrap;
  }
  .contact-icon { width: 15px; height: 15px; flex: none; }
  .front-wordmark {
    position: absolute;
    left: 372px;
    top: 150px;
    font-family: "Jost", sans-serif;
    font-weight: 400;
    font-size: 20px;
    letter-spacing: 5px;
    color: var(--ink);
  }
  /* Back */
  .card-back {
    background: var(--ink);
    display: flex;
    align-items: center;
    justify-content: center;
  }
  .back-wordmark {
    font-family: "Jost", sans-serif;
    font-weight: 400;
    font-size: 30px;
    letter-spacing: 10px;
    color: var(--mist);
    padding-left: 10px;
  }
</style>
</head>
<body>
<main class="canvas">
  <section class="card card-front" aria-label="Card front">
    <div class="front-corner-block"></div>
    <div class="person">
      <p class="person-name">Liora Quenby</p>
      <p class="person-title">Chief Financial Officer</p>
    </div>
    <ul class="contact-band">
      <li class="contact-item">
        <svg class="contact-icon" viewBox="0 0 16 16" aria-hidden="true">
          <circle cx="8" cy="8" r="8" fill="#ffffff"/>
          <path d="M5.2 3.8l1.4 1.9-.8 1c.5 1.1 1.3 1.9 2.4 2.4l1-.8 1.9 1.4-.8 1.4c-2.8-.2-5.7-3.1-5.9-5.9z" fill="#0b0708"/>
        </svg>
        780-555-0142
      </li>
      <li class="contact-item">
        <svg class="contact-icon" viewBox="0 0 16 16" aria-hidden="true">
          <rect x="0.5" y="3" width="15" height="10" fill="#ffffff"/>
          <path d="M1 3.5l7 5 7-5" fill="none" stroke="#0b0708" stroke-width="1.2"/>
        </svg>
        lioraquenby@bellhavengroup.example
      </li>
      <li class="contact-item">
        <svg class="contact-icon" viewBox="0 0 16 16" aria-hidden="true">
          <circle cx="8" cy="8" r="7.5" fill="#ffffff"/>
          <g fill="none" stroke="#0b0708" stroke-width="0.9">
            <ellipse cx="8" cy="8" rx="3" ry="6.5"/>
            <path d="M1.5 8h13M2.5 5h11M2.5 11h11M8 1.5v13"/>
          </g>
        </svg>
        www.bellhavengroup.example
      </li>
    </ul>
    <p class="front-wordmark">BELLHAVEN</p>
  </section>

  <section class="card card-back" aria-label="Card back">
    <p class="back-wordmark">BELLHAVEN</p>
  </section>
</main>
</body>
</html>
```